Business Card Design Project

We have recently completed CraftHive projects for a new logo and wesbite.
We now require new business cards.
We hand out very little printed material to clients as all information is online. When we do hand out something, like a business card, we want it to have real impact and make a statement about the quality and professionalism of our company.
We have an idea of what we want our card to look like but we want a designer to make sure they have impact and look great.
Our requirements are…
Size: 85mm X 55mm - Landscape
Front of card: Logo plus the following contact information.
Dennis Marlow
Operations Manager
Phone +44(0) 1632 xxx xxx
Mobile +44(0) 7700 xxx xxx
Email denmo@korvantix.example
Address 17 Pellick Row, Aberdeen AB12 9QZ
Website www.korvantix.example
How you layout the front of the card is up to you, we would like to see some different ideas. Attached are two versions of our logo that may be used.
Back of card: We would like this to be simple but again have impact. Our current thought is to have the logo or just the large W design from the logo in white against a dark background, perhaps made up from the dark green in the logo.
The logos are attached so you can see the colours in them but the dark ones are..
Dark Blue = C:88, M:55, Y:44, K:28
Dark Green = C:87, M:53, Y:50, K:50
We sometimes also use a bright orange as an accent or highlight colour…
Orange: = C:0, M:39, Y:94, K:0

```html
<!DOCTYPE html>
<html lang="en">
<head>
<meta charset="utf-8">
<title>Korvantix — Business Card Concepts</title>
<link rel="stylesheet" href="https://fonts.googleapis.com/css2?family=Open+Sans:wght@400;600;700;800&display=swap">
<style>
  :root {
    --backdrop: #7d5739;
    --label-ink: #24160c;
    --card-dark: #123f47;
    --card-light: #ffffff;
    --ink-white: #ffffff;
    --ink-soft: #c9dadc;
    --ink-teal: #1d4752;
    --ink-url: #3b4a55;
    --faint-teal: #4f8590;
    --accent-orange: #f7a11a;
    --rule: rgba(255,255,255,0.35);
  }
  * { margin: 0; padding: 0; box-sizing: border-box; }
  html, body { width: 1200px; height: 788px; overflow: hidden; }
  body {
    position: relative;
    background: var(--backdrop);
    font-family: "Open Sans", Arial, sans-serif;
  }
  .view-label {
    position: absolute;
    width: 503px;
    text-align: center;
    font-size: 21px;
    color: var(--label-ink);
  }
  .card {
    position: absolute;
    width: 503px;
    height: 324px;
    border-radius: 22px;
    overflow: hidden;
  }
  .card--dark { background: var(--card-dark); }
  .card--light { background: var(--card-light); }

  .card--front { left: 65px; top: 55px; }
  .card--back-1 { left: 625px; top: 55px; }
  .card--back-2 { left: 65px; top: 444px; }
  .card--back-3 { left: 625px; top: 444px; }

  .brand-name {
    position: absolute;
    display: flex;
    align-items: center;
    gap: 12px;
    font-weight: 800;
    letter-spacing: -0.5px;
    white-space: nowrap;
  }
  .brand-mark { display: inline-block; border-radius: 50%; }

  .card--front .brand-name {
    left: 34px; top: 70px;
    font-size: 40px;
    color: var(--ink-white);
  }
  .card--front .brand-mark { width: 22px; height: 22px; background: var(--ink-white); }

  .holder {
    position: absolute;
    right: 30px; top: 218px;
    text-align: right;
  }
  .holder-name { font-size: 17px; font-weight: 700; color: var(--ink-white); line-height: 1.2; }
  .holder-role { font-size: 13px; color: var(--ink-soft); line-height: 1.4; }
  .contact-rule {
    position: absolute;
    left: 25px; right: 30px; top: 262px;
    height: 1px; background: var(--rule);
  }
  .contact {
    position: absolute;
    font-size: 12px;
    color: var(--ink-white);
    line-height: 21px;
    white-space: nowrap;
  }
  .contact-col--phones { left: 25px; top: 265px; }
  .contact-col--web { left: 177px; top: 265px; }
  .contact-col--address { right: 30px; top: 267px; text-align: right; line-height: 20px; }
  .contact-item { display: flex; align-items: center; gap: 6px; }
  .contact-item svg { width: 11px; height: 11px; flex: none; }

  .card--back-1 .brand-name {
    left: 0; right: 0; top: 105px; justify-content: center;
    font-size: 52px; color: var(--ink-teal);
  }
  .card--back-1 .brand-mark,
  .card--back-3 .brand-mark { width: 26px; height: 26px; background: var(--ink-teal); }
  .web-address {
    position: absolute;
    left: 0; right: 0;
    text-align: center;
    font-size: 18px;
    letter-spacing: 3px;
    color: var(--ink-url);
  }
  .card--back-1 .web-address { top: 282px; }

  .card--back-2 .brand-name {
    left: 0; right: 0; top: 120px; justify-content: center;
    font-size: 64px; color: var(--faint-teal);
  }

  .card--back-3 .brand-name {
    left: 0; right: 0; top: 145px; justify-content: center;
    font-size: 52px; color: var(--ink-teal);
  }
  .card--back-3 .web-address { top: 278px; }
</style>
</head>
<body>

  <p class="view-label" style="left:65px; top:18px;">Front</p>
  <p class="view-label" style="left:625px; top:18px;">Back - 1</p>
  <p class="view-label" style="left:65px; top:401px;">Back - 2</p>
  <p class="view-label" style="left:625px; top:401px;">Back - 3</p>

  <section class="card card--dark card--front" aria-label="Card front">
    <div class="brand-name"><span class="brand-mark"></span>Korvantix</div>

    <div class="holder">
      <p class="holder-name">Dennis Marlow</p>
      <p class="holder-role">Operations Manager</p>
    </div>
    <div class="contact-rule"></div>

    <div class="contact contact-col--phones">
      <p class="contact-item">
        <svg viewBox="0 0 12 12" aria-hidden="true"><path d="M3 1 L5 3 L4 5 Q5.5 7.5 7 8 L9 7 L11 9 L9.5 11 Q3 10 1 2.5 Z" fill="#fff"/></svg>
        +44(0) 1632 xxxxxx
      </p>
      <p class="contact-item">
        <svg viewBox="0 0 12 12" aria-hidden="true"><rect x="3" y="0.5" width="6" height="11" rx="1" fill="#fff"/><rect x="4" y="2" width="4" height="5" fill="#123f47"/></svg>
        +44(0) 7700 xxxxxx
      </p>
    </div>

    <div class="contact contact-col--web">
      <p class="contact-item">
        <svg viewBox="0 0 12 12" aria-hidden="true"><rect x="0.5" y="2.5" width="11" height="7" rx="1" fill="#fff"/><path d="M1 3 L6 7 L11 3" stroke="#123f47" fill="none" stroke-width="1"/></svg>
        denmo@korvantix.example
      </p>
      <p class="contact-item">
        <svg viewBox="0 0 12 12" aria-hidden="true"><circle cx="6" cy="6" r="4.5" fill="#fff"/></svg>
        www.korvantix.example
      </p>
    </div>

    <address class="contact contact-col--address" style="font-style:normal;">
      17 Pellick Row<br>Aberdeen AB12 9QZ
    </address>
  </section>

  <section class="card card--light card--back-1" aria-label="Card back, option 1">
    <div class="brand-name"><span class="brand-mark"></span>Korvantix</div>
    <p class="web-address">www.korvantix.example</p>
  </section>

  <section class="card card--dark card--back-2" aria-label="Card back, option 2">
    <div class="brand-name">Korvantix</div>
  </section>

  <section class="card card--light card--back-3" aria-label="Card back, option 3">
    <div class="brand-name"><span class="brand-mark"></span>Korvantix</div>
    <p class="web-address">www.korvantix.example</p>
  </section>

</body>
</html>
```